Quorimo Business Card Design Project

We need a business card design for quorimo.example a company based in Berlin, Germany.

?Quorimo is marketplace that enables people all over the world to monetize and exchange their individual knowledge and language skills through interactive video sessions. User are matched by their interests.

On Quorimo everybody can be student or teacher (seller or buyer).

We would love to see designs that use or main color blue and green. The design should communicate what Quorimo enables - see my notice above.

Looking so forward to your designs
Cheers from Berlin,
Lorenz

Target Market(s)

globally

Industry/Entity Type

Teacher

Requirements
Must have
• Lorenz Hubeck
CEO
Quorimo.example

Quorimo e-Services GmbH
Lindenweg 87
10247 Berlin

Fon: +49 30 418 906 25 17
Mobile: 49 172 54 91 37 6
E-Mail: l.hubeck@quorimo.example
Web: www.quorimo.example

```html
<!DOCTYPE html>
<html lang="en">
<head>
<meta charset="utf-8">
<title>Quorimo Business Cards</title>
<link rel="stylesheet" href="https://fonts.googleapis.com/css2?family=Source+Sans+3:wght@400;600;700&display=swap">
<style>
  :root {
    --brand-blue: #00a3e0;
    --brand-green: #8cc63f;
    --text-grey: #5b5b5b;
    --ink-dark: #1d2a36;
    --card-white: #ffffff;
    --backdrop: #efefef;
  }
  * { margin: 0; padding: 0; box-sizing: border-box; }
  html, body { width: 1200px; height: 473px; overflow: hidden; }
  body {
    position: relative;
    background: var(--backdrop);
    font-family: "Source Sans 3", "Myriad Pro", Arial, sans-serif;
  }
  .card {
    position: absolute;
    top: 83px;
    width: 523px;
    height: 299px;
    overflow: hidden;
    box-shadow: 0 2px 6px rgba(0,0,0,0.18);
  }
  .card--front { left: 44px; background: var(--card-white); }
  .card--back { left: 613px; background: var(--brand-blue); }

  .brand { position: absolute; }
  .brand__mark { position: absolute; left: 0; top: 0; width: 44px; height: 44px; }
  .brand__name {
    position: absolute;
    font-weight: 400;
    line-height: 1;
    white-space: nowrap;
  }
  .brand__tagline {
    position: absolute;
    font-weight: 600;
    letter-spacing: 1.6px;
    white-space: nowrap;
  }
  .card--front .brand { left: 28px; top: 122px; }
  .card--front .brand__mark { background: var(--brand-blue); top: 3px; }
  .card--front .brand__name { left: 52px; top: 0; font-size: 44px; color: var(--text-grey); }
  .card--front .brand__tagline { left: 56px; top: 40px; font-size: 11px; color: var(--brand-blue); }

  .divider {
    position: absolute; left: 279px; top: 112px; width: 1px; height: 76px;
    background: linear-gradient(to bottom, rgba(120,120,120,0), #8a8a8a 50%, rgba(120,120,120,0));
  }

  .contact { position: absolute; left: 311px; top: 61px; }
  .contact__name { font-size: 16px; font-weight: 700; color: var(--brand-blue); line-height: 20px; }
  .contact__role { font-size: 12px; color: var(--text-grey); line-height: 16px; }
  .contact__list { list-style: none; margin-top: 20px; }
  .contact__item {
    display: flex; align-items: center; gap: 9px;
    font-size: 13px; color: var(--text-grey); line-height: 19px;
  }
  .contact__icon { width: 11px; height: 11px; fill: var(--text-grey); flex: none; }
  .contact__icon--globe { fill: none; stroke: var(--text-grey); stroke-width: 1.1; }

  .swoosh { position: absolute; left: 0; bottom: 0; width: 523px; height: 80px; }
  .company-line {
    position: absolute; left: 51px; bottom: 10px;
    font-size: 13px; color: var(--card-white); white-space: nowrap;
  }

  .card--back .brand { left: 120px; top: 101px; }
  .card--back .brand__mark { background: var(--card-white); width: 44px; height: 56px; }
  .card--back .brand__name { left: 52px; top: 0; font-size: 58px; color: var(--card-white); }
  .card--back .brand__tagline { left: 90px; top: 50px; font-size: 13px; color: var(--card-white); }
  .back-web {
    position: absolute; left: 0; right: 0; top: 246px; text-align: center;
    font-size: 12px; letter-spacing: 2.4px; color: var(--ink-dark);
  }
</style>
</head>
<body>

<section class="card card--front" aria-label="Business card front">
  <div class="brand">
    <span class="brand__mark"></span>
    <span class="brand__name">quorimo</span>
    <span class="brand__tagline">share what you know</span>
  </div>

  <div class="divider"></div>

  <div class="contact">
    <p class="contact__name">Lorenz Hubeck</p>
    <p class="contact__role">CEO</p>
    <ul class="contact__list">
      <li class="contact__item">
        <svg class="contact__icon" viewBox="0 0 12 12"><path d="M2.5 0.5l2 2.6-1.1 1.2c.6 1.5 1.8 2.7 3.3 3.3l1.2-1.1 2.6 2-1 1.9C5 10.2 1.8 7 1 2.5z"/></svg>
        <span>+49 30 418 906 25 17</span>
      </li>
      <li class="contact__item">
        <svg class="contact__icon" viewBox="0 0 12 12"><path d="M3 0h6v12H3zM4 1.5v7h4v-7zM5.4 9.6h1.2v1.2H5.4z" fill-rule="evenodd"/></svg>
        <span>49 172 54 91 37 6</span>
      </li>
      <li class="contact__item">
        <svg class="contact__icon" viewBox="0 0 12 12"><path d="M0 2.5h12v7H0zM0.6 3l5.4 3.6L11.4 3v0.9L6 7.5 0.6 3.9z" fill-rule="evenodd"/></svg>
        <span>l.hubeck@quorimo.example</span>
      </li>
      <li class="contact__item">
        <svg class="contact__icon contact__icon--globe" viewBox="0 0 12 12">
          <circle cx="6" cy="6" r="5"/>
          <ellipse cx="6" cy="6" rx="2.2" ry="5"/>
          <path d="M1 6h10M2 3.3h8M2 8.7h8"/>
        </svg>
        <span>www.quorimo.example</span>
      </li>
    </ul>
  </div>

  <svg class="swoosh" viewBox="0 0 523 80" preserveAspectRatio="none" aria-hidden="true">
    <path d="M0 31 Q230 -4 523 38 L523 45 Q230 6 0 36 Z" fill="var(--brand-green)"/>
    <path d="M0 39 Q230 10 523 49 L523 80 L0 80 Z" fill="var(--brand-blue)"/>
  </svg>
  <p class="company-line">Quorimo e-Services GmbH&nbsp; Lindenweg 87 10247 Berlin</p>
</section>

<section class="card card--back" aria-label="Business card back">
  <div class="brand">
    <span class="brand__mark"></span>
    <span class="brand__name">quorimo</span>
    <span class="brand__tagline">share what you know</span>
  </div>
  <p class="back-web">www.quorimo.example</p>
</section>

</body>
</html>
```